Business Cards for IT Consulting Company (Managed Service Provider)

I am looking to have some business cards printed and would like some designs. We are an IT Consulting company based in Vancouver BC. I would like a nice clean and modern look to the cards. I have uploaded all the versions of my logo so parts can be used as needed. Here is a snippit from our website homepage:

Quillbrook Networks Ltd. is an IT Solutions Partner located in Vancouver BC, Canada. We offer IT solutions and support to customers in the greater Vancouver Area. With expertise in Microsoft platforms, as well as Linux and Mac OSX and over 12 years experience in the IT industry, Quillbrook Networks is dedicated to offering our clients top quality service and products. We take pride in the solutions we offer our customers. The greatest compliment a client can give us is to recommend our services.

Quillbrook Networks Ltd. offers a wide range of IT services from onsite service to remote support and managed service solutions. This allows clients to choose the support path that best suits their company’s needs. Supporting many different sized companies from small to enterprise level over the past 12 years Quillbrook Networks has the experience and expertise needed to ensure things run smoothly. Allowing our clients to focus on doing business.

Revolutionizing the way IT services are delivered.

Quillbrook Networks is dedicated to providing our clients with IT solutions that work and grow with them for years to come. This philosophy helps save money in the long run instead of replacing equipment constantly. Far too often IT solutions are not well thought out and while possibly solving the problem at hand, require replacement due to growth or quality within a very short time frame. Quillbrook Networks takes pride in providing solutions that will last and be able to accommodate growth without the need for replacement.

Industry/Entity Type

Information Technology

Contact Information for Business Card

Quillbrook Networks Ltd.
(Employee Name)
Eml: (Employees Email Address)
Web: quillbrook.me
Ph: 604-555-0148

Font styles to use
Serif
Sans Serif

Requirements
Must have
• The Company logo and company colors.
Nice to have
• - Our tag line: "Revolutionizing IT Services" or "Revolutionizing the way IT services are delivered."
• - Also I really like the idea of nature and technology together blending which is sort of where my logo came from so integrating that somehow onto the business cards would be great.

```html
<!DOCTYPE html>
<html lang="en">
<head>
<meta charset="utf-8">
<title>Quillbrook Networks Ltd. — Business Card</title>
<link rel="stylesheet" href="https://fonts.googleapis.com/css2?family=Open+Sans:wght@400;600;700&display=swap">
<style>
  :root {
    --stage: #141414;
    --paper: #ffffff;
    --brand-blue: #00a3e0;
    --back-blue: #0a9ad8;
    --ink-grey: #58595b;
    --tab-grey: #5e5f62;
    --white: #ffffff;
  }
  * { box-sizing: border-box; margin: 0; padding: 0; }
  html, body {
    width: 1200px; height: 900px; overflow: hidden;
    background: var(--stage);
    font-family: "Open Sans", Arial, sans-serif;
  }
  .canvas { position: relative; width: 1200px; height: 900px; }

  .card { position: absolute; top: 170px; width: 347px; height: 561px; overflow: hidden; }

  /* Front */
  .card-front { left: 259px; background: var(--paper); text-align: center; }
  .tab { position: absolute; left: 102px; width: 143px; }
  .tab-top { top: 0; height: 30px; background: var(--brand-blue); }
  .tab-bottom { bottom: 0; height: 28px; background: var(--tab-grey); }

  .brand { position: absolute; top: 100px; left: 0; width: 100%; }
  .brand-name {
    font-size: 46px; font-weight: 600; letter-spacing: -0.5px;
    color: var(--brand-blue); line-height: 1;
  }
  .brand-sub {
    margin-top: 6px; font-size: 16px; font-weight: 600; letter-spacing: 1px;
    color: var(--brand-blue);
  }
  .tagline {
    position: absolute; top: 181px; left: 0; width: 100%;
    font-size: 17px; font-weight: 600; color: var(--ink-grey);
  }
  .tagline .accent { color: var(--brand-blue); }

  .person {
    position: absolute; top: 396px; left: 0; width: 100%;
    font-size: 20px; font-weight: 600; color: var(--ink-grey);
  }
  .person .first { color: var(--brand-blue); }

  .contact {
    position: absolute; top: 450px; left: 0; width: 100%;
    list-style: none; font-size: 14.5px; line-height: 23px; color: var(--ink-grey);
  }
  .contact .label { color: var(--brand-blue); font-weight: 700; }

  /* Back */
  .card-back { left: 631px; background: var(--back-blue); }
  .back-brand { position: absolute; left: 28px; bottom: 40px; color: var(--white); }
  .back-brand .brand-name { color: var(--white); font-size: 62px; font-weight: 600; letter-spacing: -0.5px; }
  .back-brand .brand-sub { color: var(--white); font-size: 20px; letter-spacing: 1.5px; margin-top: 4px; }
</style>
</head>
<body>
<main class="canvas">
  <section class="card card-front" aria-label="Card front">
    <div class="tab tab-top"></div>
    <div class="brand">
      <div class="brand-name">quillbrook</div>
      <div class="brand-sub">NETWORKS LTD.</div>
    </div>
    <p class="tagline"><span class="accent">Revolutionizing</span> IT Services</p>
    <p class="person"><span class="first">Daniel</span> Hartley</p>
    <ul class="contact">
      <li><span class="label">T:</span> 604-555-0148</li>
      <li><span class="label">E:</span> info@quillbrook.me</li>
      <li><span class="label">W:</span> www.quillbrook.me</li>
    </ul>
    <div class="tab tab-bottom"></div>
  </section>

  <section class="card card-back" aria-label="Card back">
    <div class="back-brand">
      <div class="brand-name">quillbrook</div>
      <div class="brand-sub">NETWORKS LTD.</div>
    </div>
  </section>
</main>
</body>
</html>
```